Boutique custom software development company needs new business card

Our nearly 20 year old custom software development company would like to better include the fact that we are now providing Bitcoin services. These new services are B2B include education (how to acquire and securely hold Bitcoin) and integrating Bitcoin payments into existing ecommerce sites or other existing systems. Please keep the card clean and simple. Attached is our current design and some other files. vextorial.com

Target Market(s)

businesses owners interested in long term relationship

Industry/Entity Type

Custom software development and Bitcoin

Contact Information for Business Card

Dale Parker, dale@vextorial.com, vextorial.com, (888) 555-VXTRL

Font styles to use
Other font styles liked:
• monospace

Requirements
Must have
• double-sided
Nice to have
• clean and simple
Should not have
• physical address

```html
<!DOCTYPE html>
<html lang="en">
<head>
<meta charset="utf-8">
<title>Vextorial Business Card</title>
<link rel="stylesheet" href="https://fonts.googleapis.com/css2?family=Lato:wght@400;700&family=Montserrat:wght@400;700;800&display=swap">
<style>
  :root {
    --ground: #9a9a9a;
    --paper: #f7f7f5;
    --brand-blue: #3b72b8;
    --brand-orange: #ee7d22;
    --ink-gray: #4a4a4a;
    --white: #ffffff;
  }
  * { margin: 0; padding: 0; box-sizing: border-box; }
  html, body { width: 1200px; height: 952px; overflow: hidden; }
  body {
    background: var(--ground);
    display: flex;
    flex-direction: column;
    align-items: center;
    justify-content: center;
    gap: 56px;
    font-family: "Montserrat", sans-serif;
  }
  .card {
    position: relative;
    width: 630px;
    height: 360px;
    border-radius: 3px;
    overflow: hidden;
    box-shadow: 0 10px 28px rgba(0,0,0,0.28);
  }
  .card-front { background: var(--paper); }
  .card-back {
    background: var(--brand-blue);
    border-bottom: 4px solid var(--brand-orange);
  }

  .brand { position: absolute; }
  .brand-name {
    display: flex;
    align-items: center;
    gap: 10px;
    font-family: "Montserrat", sans-serif;
    font-weight: 800;
    letter-spacing: 0.5px;
    line-height: 1;
  }
  .brand-mark { display: block; background: var(--brand-orange); }
  .brand-tagline {
    font-family: "Lato", sans-serif;
    font-weight: 400;
    margin-top: 6px;
  }

  .card-front .brand { left: 46px; top: 118px; }
  .card-front .brand-name { font-size: 42px; color: var(--brand-blue); }
  .card-front .brand-mark { width: 26px; height: 26px; }
  .card-front .brand-tagline { font-size: 16px; color: var(--brand-blue); padding-left: 2px; }
  .card-front .service-line {
    font-family: "Lato", sans-serif;
    font-weight: 700;
    font-size: 13px;
    color: var(--brand-orange);
    margin-top: 5px;
    padding-left: 2px;
    letter-spacing: 0.3px;
  }

  .divider {
    position: absolute;
    left: 340px; top: 92px;
    width: 1.5px; height: 150px;
    background: var(--brand-orange);
  }

  .contact-block { position: absolute; left: 370px; top: 100px; }
  .person-name {
    font-weight: 700;
    font-size: 22px;
    letter-spacing: 2px;
    text-transform: uppercase;
    line-height: 1;
  }
  .person-first { color: var(--brand-orange); }
  .person-last { color: var(--brand-blue); }
  .person-role {
    font-size: 14px;
    color: var(--ink-gray);
    letter-spacing: 1px;
    margin-top: 4px;
  }
  .contact-list { list-style: none; margin-top: 20px; }
  .contact-item {
    display: flex;
    align-items: center;
    gap: 8px;
    font-size: 13.5px;
    color: var(--ink-gray);
    letter-spacing: 0.8px;
    margin-bottom: 7px;
  }
  .contact-icon { width: 12px; height: 12px; flex: none; }

  .edge-stripes { position: absolute; left: 0; right: 0; bottom: 0; }
  .stripe-thin { height: 3px; background: var(--brand-orange); }
  .stripe-gap { height: 5px; background: var(--paper); }
  .stripe-band { height: 10px; background: var(--brand-blue); }
  .stripe-edge { height: 4px; background: var(--brand-orange); }

  .card-back .brand { left: 62px; top: 104px; }
  .card-back .brand-name { font-size: 54px; color: var(--white); }
  .card-back .brand-mark { width: 32px; height: 32px; }
  .card-back .brand-tagline { font-size: 20px; color: var(--white); padding-left: 2px; }
  .service-rule {
    width: 48px; height: 3px;
    background: var(--brand-orange);
    margin: 18px 0 12px 2px;
  }
  .service-list {
    list-style: none;
    padding-left: 2px;
    font-family: "Lato", sans-serif;
    font-size: 15px;
    color: var(--white);
    line-height: 1.5;
  }
  .service-list strong { font-weight: 700; }
</style>
</head>
<body>
  <section class="card card-front" aria-label="Business card front">
    <div class="brand">
      <div class="brand-name"><span class="brand-mark"></span>Vextorial</div>
      <div class="brand-tagline">developer of custom applications</div>
      <div class="service-line">&amp; Bitcoin services for business</div>
    </div>

    <div class="divider"></div>

    <div class="contact-block">
      <div class="person-name"><span class="person-first">Dale</span> <span class="person-last">Parker</span></div>
      <div class="person-role">Owner</div>
      <ul class="contact-list">
        <li class="contact-item">
          <svg class="contact-icon" viewBox="0 0 24 24" aria-hidden="true"><path fill="#3b72b8" d="M6.6 10.8a15.1 15.1 0 0 0 6.6 6.6l2.2-2.2c.3-.3.7-.4 1-.2 1.1.4 2.3.6 3.6.6.6 0 1 .4 1 1V20c0 .6-.4 1-1 1A17 17 0 0 1 3 4c0-.6.4-1 1-1h3.5c.6 0 1 .4 1 1 0 1.3.2 2.5.6 3.6.1.3 0 .7-.2 1z"/></svg>
          (888) 555-VXTRL
        </li>
        <li class="contact-item">
          <svg class="contact-icon" viewBox="0 0 24 24" aria-hidden="true"><rect x="2" y="5" width="20" height="14" fill="#3b72b8"/><path d="M2 5l10 8 10-8" fill="none" stroke="#f7f7f5" stroke-width="1.6"/></svg>
          dale@vextorial.com
        </li>
        <li class="contact-item">
          <svg class="contact-icon" viewBox="0 0 24 24" aria-hidden="true"><circle cx="12" cy="12" r="10" fill="#3b72b8"/><path d="M2 12h20M12 2c3 3 3 17 0 20M12 2c-3 3-3 17 0 20" fill="none" stroke="#f7f7f5" stroke-width="1.4"/></svg>
          www.vextorial.com
        </li>
      </ul>
    </div>

    <div class="edge-stripes">
      <div class="stripe-thin"></div>
      <div class="stripe-gap"></div>
      <div class="stripe-band"></div>
      <div class="stripe-edge"></div>
    </div>
  </section>

  <section class="card card-back" aria-label="Business card back">
    <div class="brand">
      <div class="brand-name"><span class="brand-mark"></span>Vextorial</div>
      <div class="brand-tagline">developer of custom applications</div>
      <div class="service-rule"></div>
      <ul class="service-list">
        <li><strong>Bitcoin education</strong> — acquire &amp; securely hold</li>
        <li><strong>Bitcoin payments</strong> — integrated into your systems</li>
      </ul>
    </div>
  </section>
</body>
</html>
```